business card

Business card for new business.
Red and black corporate colors.
Card can have an Indsutrial feel to it. Feel free to add Rust, Bolted steel, or graphics as you see fit. We provide highly specialized services to the below mentioned industries.
Keep information out of corners so that if I want I can choose rounded corners.
Information
- front. name - title - phone - email
- Rear
Forging - Marine - Heavy Haulage - Quarrying - Power
Halden - Brookmere - Port Ashcombe - Ridgeton - Lakeford

```html
<!DOCTYPE html>
<html lang="en">
<head>
<meta charset="utf-8">
<title>Girderline Business Card</title>
<link rel="stylesheet" href="https://fonts.googleapis.com/css2?family=Roboto:wght@400;700&family=Roboto+Condensed:wght@700&display=swap">
<style>
  :root {
    --backdrop: #e9e7e3;
    --card-white: #ffffff;
    --card-paper: #f4f4f4;
    --steel-grey: #7b7b7b;
    --signal-red: #e3001b;
    --ink: #4d4d4d;
    --wordmark-grey: #757575;
  }
  * { margin: 0; padding: 0; box-sizing: border-box; }
  html, body {
    width: 1200px;
    height: 960px;
    overflow: hidden;
    background: var(--backdrop);
    font-family: "Roboto", Arial, sans-serif;
  }
  .canvas { position: relative; width: 1200px; height: 960px; }

  /* Front card */
  .card-front {
    position: absolute;
    left: 314px; top: 113px;
    width: 600px; height: 343px;
    background: var(--card-white);
    padding: 5px;
  }
  .card-front__panel {
    position: relative;
    width: 100%; height: 100%;
    background: var(--steel-grey);
  }
  .brand-mark {
    position: absolute;
    left: 38px; top: 38px;
    display: flex; align-items: center; gap: 8px;
    color: var(--signal-red);
    font-weight: 700;
    font-size: 22px;
    letter-spacing: 0.5px;
  }
  .brand-mark__square {
    width: 14px; height: 14px;
    background: var(--signal-red);
  }
  .identity {
    position: absolute;
    right: 35px; top: 226px;
    display: flex; align-items: baseline; gap: 16px;
  }
  .identity__title {
    color: var(--card-white);
    font-size: 15px;
  }
  .identity__name {
    color: var(--signal-red);
    font-family: "Roboto Condensed", "Arial Narrow", sans-serif;
    font-weight: 700;
    font-size: 23px;
  }
  .identity__arrow {
    position: absolute;
    right: 35px; top: 254px;
  }
  .contact {
    position: absolute;
    right: 35px; top: 271px;
    color: var(--card-white);
    font-size: 14.5px;
    line-height: 19px;
    text-align: right;
  }

  /* Rear card */
  .card-rear {
    position: absolute;
    left: 311px; top: 472px;
    width: 600px; height: 343px;
    background: var(--card-paper);
  }
  .wordmark {
    position: absolute;
    left: 0; right: 0; top: 128px;
    display: flex; justify-content: center; align-items: center; gap: 12px;
    color: var(--wordmark-grey);
    font-weight: 700;
    font-size: 48px;
    letter-spacing: 1px;
  }
  .wordmark__square {
    width: 20px; height: 20px;
    background: var(--signal-red);
  }
  .services {
    position: absolute;
    left: 0; right: 0; top: 256px;
    text-align: center;
    color: var(--ink);
    font-size: 14.5px;
    line-height: 18px;
  }
  .services__dot {
    display: inline-block;
    width: 4px; height: 4px;
    margin: 0 3px 3px;
    border-radius: 50%;
    background: var(--signal-red);
    vertical-align: middle;
  }
</style>
</head>
<body>
<main class="canvas">
  <section class="card-front" aria-label="Card front">
    <div class="card-front__panel">
      <div class="brand-mark">
        <span class="brand-mark__square"></span>
        <span class="brand-mark__name">GIRDERLINE</span>
      </div>
      <div class="identity">
        <span class="identity__title">CEO/FOUNDER</span>
        <span class="identity__name">DANIEL REYES</span>
      </div>
      <svg class="identity__arrow" width="36" height="8" viewBox="0 0 36 8" aria-hidden="true">
        <line x1="0" y1="4" x2="30" y2="4" stroke="#e3001b" stroke-width="1.6"/>
        <polygon points="29,0.5 36,4 29,7.5" fill="#e3001b"/>
      </svg>
      <div class="contact">
        <p class="contact__phone">555 014 2290</p>
        <p class="contact__web">info@girderline.com | www.girderline.com</p>
      </div>
    </div>
  </section>

  <section class="card-rear" aria-label="Card back">
    <div class="wordmark">
      <span class="wordmark__square"></span>
      <span class="wordmark__name">GIRDERLINE</span>
    </div>
    <div class="services">
      <p>Forging<span class="services__dot"></span>Marine<span class="services__dot"></span>Heavy Haulage<span class="services__dot"></span>Quarrying</p>
      <p>Power<span class="services__dot"></span>Halden<span class="services__dot"></span>Brookmere<span class="services__dot"></span>Port Ashcombe</p>
      <p>Ridgeton<span class="services__dot"></span>Lakeford</p>
    </div>
  </section>
</main>
</body>
</html>
```